real esate business card with company logo and name

we need a business card design for a real esate company

The company name is Walsh & Brand Pty Ltd, and we have our logo designed and will upload. We want classic or moden feel. Black or white background. looks more textured. Should include folowinginformations
Owen Walsh and Lucy Brand
Sales Agents & Onsite Manager
p: 07 5948 2063
F: 07 5948 2174
M:0431 857 219
3/42 Marlow Crescent, FERNLEA QLD 4213

We want this business card looks professonal. Thank you in advance.

Industry/Entity Type

Real Estate Agent

Contact Information for Business Card

Owen Walsh and Lucy Brand
Onsite Manager & Sales Agents
p: 07 5948 2063
M:0431 857 219

Font styles to use
Serif

Colors
000000
fbfbfb
333333
959595

Requirements
Must have
• company logo and name, black or white back ground

```html
<!DOCTYPE html>
<html lang="en">
<head>
<meta charset="utf-8">
<title>Walsh &amp; Brand Pty Ltd – Business Card</title>
<link rel="stylesheet" href="https://fonts.googleapis.com/css2?family=Alegreya+Sans:wght@400;700;800&display=swap">
<style>
  :root {
    --ink: #000000;
    --paper: #fbfbfb;
    --charcoal: #333333;
    --mid-grey: #959595;
    --label-grey: #6f6f6f;
    --brand-grey: #6a6a6a;
    --shade: #8c8c8c;
  }
  html, body {
    margin: 0;
    padding: 0;
    width: 1200px;
    height: 686px;
    overflow: hidden;
    background: var(--paper);
  }
  .card {
    position: relative;
    width: 1200px;
    height: 686px;
    overflow: hidden;
    font-family: "Alegreya Sans", sans-serif;
    background:
      radial-gradient(ellipse 75% 95% at 12% 60%, #ffffff 0%, #fbfbfb 30%, rgba(251,251,251,0) 70%),
      linear-gradient(100deg, #fbfbfb 0%, #f0f0f0 38%, #bdbdbd 62%, #9e9e9e 82%, var(--mid-grey) 100%);
  }
  .brand {
    position: absolute;
    left: 80px;
    top: 130px;
    width: 440px;
    display: flex;
    flex-direction: column;
    align-items: center;
  }
  .brand__square {
    width: 170px;
    height: 170px;
    background: var(--shade);
    margin-bottom: 120px;
  }
  .brand__name {
    margin: 0;
    font-size: 33px;
    font-weight: 700;
    letter-spacing: 1px;
    color: var(--brand-grey);
    white-space: nowrap;
  }
  .agents {
    position: absolute;
    left: 596px;
    top: 82px;
    width: 520px;
  }
  .agents__names {
    margin: 0;
    font-size: 41px;
    font-weight: 800;
    color: var(--ink);
    line-height: 1;
    white-space: nowrap;
  }
  .agents__role {
    margin: 6px 0 0 27px;
    font-size: 24px;
    font-weight: 700;
    color: var(--label-grey);
    white-space: nowrap;
  }
  .contact {
    position: absolute;
    right: 65px;
    top: 420px;
    margin: 0;
    padding: 0;
    list-style: none;
    text-align: right;
    font-size: 34px;
    font-weight: 800;
    color: var(--ink);
    line-height: 50px;
  }
  .contact__label {
    color: var(--label-grey);
    margin-right: 14px;
  }
  .contact__label--tight { margin-right: 6px; }
</style>
</head>
<body>
  <main class="card">
    <section class="brand">
      <div class="brand__square" aria-hidden="true"></div>
      <p class="brand__name">WALSH &amp; BRAND PTY LTD.</p>
    </section>

    <header class="agents">
      <h1 class="agents__names">Owen Walsh and Lucy Brand</h1>
      <p class="agents__role">Onsite Manager &amp; Sales Agents</p>
    </header>

    <ul class="contact">
      <li><span class="contact__label">P</span>07 5948 2063</li>
      <li><span class="contact__label">M</span>0431 857 219</li>
      <li><span class="contact__label contact__label--tight">A</span>3/42 Marlow Crescent</li>
      <li>FERNLEA QLD 4213</li>
    </ul>
  </main>
</body>
</html>
```